Willow Nest Product Marketing Sheet Front and Back

Please see the VERY VERY VERY ROUGH COMPS THAT WE DID TO LEND SOME DIRECTION TO THE PIECE- SO YOU HAVE AN IDEA OF WHAT'S IMPORTANT TO COMMUNICATE ON THE FRONT AND THE BACK.

DON'T FOLLOW OUR LAYOUT.. This is just for you to see what goes to the front and what goes to the back.. see the files that we just loaded up to the art folder!

We also have a PDF that has a check off list for items that need to be on the front and then on the back!

PROJECT SCOPE:

Project is to make a sell sheet front that is 8.5 inches wide x 11 inches tall in a 4 color design using our current Willow Nest Logo with your design talents. We also need the back of the sell sheet that has the basic instructions on how to install the Willow Nest Mattress Cover and shows the value added aspects of the product.

We need files in layered PSD format as we have various dealers that we tweak parts of our product line. We will also use these layered files as a back up for the printer in case they don't have the printer font, we can make him print ready file from your PSD file.

We have the logo, tag line, header main font selected and need you to design the look and feel of the piece.

We have all of the copy for the sell sheet- this is the only PDF file in the art file resources.

Overall this piece needs to convey a FUN, FRESH and PEACEFUL PRODUCT.. we don't want a cluttered design.

COPY IS SAVED AS: WILLOW NEST CONTENTS ( PDF FILE)
COMPS ARE SAVED AS: FRONT AND REAR COMP ( JPG FILES)
Updates

Project Deadline Extended
Reason: We have a lot of designers that have requested a few more days to submit.. so we are extending the competition. Thank you and good luck!

Target Market(s)

Corvani Consumers that are buying a mattress cover for comfort, peace of mind and to reduce night heat issues ( sweating) and to avoid dust mites, bed bugs and stains.

Industry/Entity Type

Marketing

Font styles to use
Sans Serif

Colors
f37122
f68e4e
fabb94
0393ce
33a6d7
86cae7
ffffff
add136
fbee3d

Requirements
Must have
• Our Current Logo as the center piece..
• WILLOW NEST is the brand name
• For a peaceful night sleep is the tag line
• Value Points ( see the PDF attached)
• Crisp color, Clean Fonts, Cant be cluttered.
• File Construction- Must be a PSD file 8.5 x11 and 300 DPI for printing
Nice to have
• Clean, Easy to Read and consistent from the front to the back
Should not have
• We don't want a cluttered look and feel for this marketing piece.

```html
<!DOCTYPE html>
<html lang="en">
<head>
<meta charset="utf-8">
<title>Willow Nest Sell Sheet – Front and Back</title>
<link href="https://fonts.googleapis.com/css2?family=Comfortaa:wght@400;700&family=Open+Sans:wght@400;600&display=swap" rel="stylesheet">
<style>
  :root {
    --bg: #d9d9d9;
    --paper: #ffffff;
    --mist: #eeeeef;
    --purple: #b561b5;
    --purple-deep: #9a4aa0;
    --purple-soft: #d9a3d6;
    --lilac-text: #9c72b4;
    --orange: #f37122;
    --orange-soft: #fabb94;
    --gold: #e3a91c;
    --body-text: #6f6f6f;
    --photo-light: #f4efec;
    --photo-mid: #e2d3c9;
  }
  * { box-sizing: border-box; margin: 0; padding: 0; }
  html, body { width: 1200px; height: 799px; overflow: hidden; }
  body {
    background: radial-gradient(ellipse at center, #f2f2f2 0%, var(--bg) 100%);
    font-family: "Open Sans", sans-serif;
    position: relative;
  }
  .sheet {
    position: absolute;
    top: 50px;
    width: 541px;
    height: 700px;
    background: linear-gradient(180deg, var(--paper) 0%, var(--mist) 100%);
    box-shadow: 0 6px 18px rgba(0,0,0,0.18);
    overflow: hidden;
  }
  .sheet--back { left: 39px; }
  .sheet--front { left: 620px; }
  .band { position: absolute; left: 0; width: 100%; }
  .band--top { top: 0; height: 90px; }
  .band--bottom { bottom: 0; height: 110px; }

  /* back */
  .install-title {
    position: absolute; top: 22px; left: 30px; right: 20px;
    font-family: "Comfortaa", sans-serif; font-size: 19px; color: #fff;
  }
  .step { position: absolute; width: 270px; }
  .step-head { display: flex; align-items: center; gap: 10px; margin-bottom: 6px; }
  .step-num {
    width: 36px; height: 36px; border-radius: 50%;
    border: 2px solid var(--purple-soft); color: var(--purple);
    font-family: "Comfortaa", sans-serif; font-size: 18px;
    display: flex; align-items: center; justify-content: center; flex: none;
  }
  .step-title { font-family: "Comfortaa", sans-serif; font-size: 15px; color: var(--purple); font-weight: 700; }
  .step-body { font-size: 9.5px; line-height: 1.35; color: var(--body-text); padding-left: 46px; }
  .figure {
    position: absolute;
    background: linear-gradient(160deg, #ffffff 0%, #dcdcdc 100%);
    border-radius: 4px;
    box-shadow: 0 3px 6px rgba(0,0,0,0.12);
  }

  /* front */
  .photo-hero {
    position: absolute; top: 0; right: 0; width: 400px; height: 300px;
    background: linear-gradient(100deg, rgba(255,255,255,1) 0%, var(--photo-light) 25%, var(--photo-mid) 60%, #f5f5f5 100%);
  }
  .brand { position: absolute; top: 24px; left: 26px; display: flex; align-items: center; gap: 10px; }
  .brand-dot { width: 44px; height: 44px; border-radius: 50%; background: var(--gold); }
  .brand-name { font-family: "Comfortaa", sans-serif; font-weight: 700; font-size: 17px; color: var(--gold); letter-spacing: 1px; }
  .tagline {
    position: absolute; top: 208px; left: 270px; width: 250px;
    font-family: "Comfortaa", sans-serif; font-size: 28px; line-height: 1.15; color: var(--lilac-text);
  }
  .badge { position: absolute; left: 26px; width: 112px; height: 112px; overflow: visible; }
  .badge-label { font-family: "Comfortaa", sans-serif; font-size: 7.6px; font-weight: 700; letter-spacing: 0.2px; }
  .photo-mattress {
    position: absolute; top: 330px; left: 180px; width: 340px; height: 160px;
    background: linear-gradient(180deg, #fafafa 0%, #e6e6e6 60%, #3a3a3a 61%, #2a2a2a 100%);
    border-radius: 6px;
  }
  .contact { position: absolute; top: 508px; left: 210px; font-family: "Comfortaa", sans-serif; color: var(--lilac-text); }
  .contact-phone { font-size: 27px; }
  .contact-mail { font-size: 11px; margin-top: 2px; }
</style>
</head>
<body>

<!-- BACK: installation guide -->
<section class="sheet sheet--back">
  <svg class="band band--top" viewBox="0 0 541 90" preserveAspectRatio="none">
    <path d="M0 0H541V60Q270 95 0 70Z" fill="var(--purple)"/>
    <path d="M0 70Q270 95 541 60V66Q270 102 0 76Z" fill="var(--purple-soft)"/>
  </svg>
  <h1 class="install-title">How to install the Willow Nest Mattress Cover</h1>

  <div class="figure" style="top:110px;left:40px;width:150px;height:70px;" role="img" aria-label="Mattress lying flat"></div>
  <div class="step" style="top:115px;left:240px;">
    <div class="step-head"><span class="step-num">1</span><span class="step-title">Remove old bedding</span></div>
    <p class="step-body">Lorem ipsum dolor sit amet, consectetuer adipiscing elit, sed diam nonummy.</p>
  </div>

  <div class="step" style="top:225px;left:40px;">
    <div class="step-head"><span class="step-num">2</span><span class="step-title">Stand mattress vertically</span></div>
    <p class="step-body">Lorem ipsum dolor sit amet, consectetuer adipiscing elit, sed diam nonummy nibh euismod tincidunt ut laoreet dolore magna aliquam erat volutpat.</p>
  </div>

  <div class="figure" style="top:330px;left:100px;width:110px;height:120px;" role="img" aria-label="Cover sliding down over upright mattress"></div>
  <div class="step" style="top:360px;left:240px;">
    <div class="step-head"><span class="step-num">3</span><span class="step-title">Slide cover down</span></div>
    <p class="step-body">Lorem ipsum dolor sit amet, consectetuer adipiscing elit, sed diam nonummy.</p>
  </div>

  <div class="step" style="top:470px;left:40px;">
    <div class="step-head"><span class="step-num">4</span><span class="step-title">Install cover evenly</span></div>
    <p class="step-body">Lorem ipsum dolor sit amet, consectetuer adipiscing elit, sed diam nonummy nibh euismod tincidunt ut laoreet dolore magna aliquam erat volutpat.</p>
  </div>
  <div class="figure" style="top:545px;left:360px;width:140px;height:60px;" role="img" aria-label="Mattress with fitted cover"></div>

  <svg class="band band--bottom" viewBox="0 0 541 110" preserveAspectRatio="none">
    <path d="M0 30Q270 80 541 20V110H0Z" fill="var(--purple)"/>
    <path d="M0 24Q270 74 541 14V22Q270 82 0 32Z" fill="var(--purple-soft)"/>
  </svg>
</section>

<!-- FRONT: product sell sheet -->
<section class="sheet sheet--front">
  <div class="photo-hero" role="img" aria-label="Couple sleeping peacefully in a white bed"></div>

  <div class="brand">
    <span class="brand-dot"></span>
    <span class="brand-name">WILLOW NEST</span>
  </div>

  <p class="tagline">For a peaceful night sleep</p>

  <svg class="badge" style="top:140px;" viewBox="0 0 112 112">
    <defs><path id="arcA" d="M15.6 70.7A43 43 0 1 1 96.4 70.7"/></defs>
    <circle cx="56" cy="56" r="33" fill="#fff" stroke="var(--purple)" stroke-width="3"/>
    <circle cx="56" cy="56" r="25" fill="#ece6ef" role="img" aria-label="Liquid beading on fabric"/>
    <text class="badge-label" fill="var(--purple)"><textPath href="#arcA" startOffset="50%" text-anchor="middle">FLUIDS ARE REPELLED</textPath></text>
  </svg>

  <svg class="badge" style="top:262px;" viewBox="0 0 112 112">
    <defs><path id="arcB" d="M15.6 70.7A43 43 0 1 1 96.4 70.7"/></defs>
    <circle cx="56" cy="56" r="33" fill="#fff" stroke="var(--orange)" stroke-width="3"/>
    <circle cx="56" cy="56" r="25" fill="#fde3d3"/>
    <g stroke="var(--orange)" stroke-width="2.6" fill="none" stroke-linecap="round" stroke-linejoin="round">
      <path d="M46 70q-4-4 0-8t0-8t0-8M42 50l4-4 4 4"/>
      <path d="M56 70q-4-4 0-8t0-8t0-8M52 50l4-4 4 4"/>
      <path d="M66 70q-4-4 0-8t0-8t0-8M62 50l4-4 4 4"/>
    </g>
    <text class="badge-label" fill="var(--orange)"><textPath href="#arcB" startOffset="50%" text-anchor="middle">AIR PASSES THROUGH</textPath></text>
  </svg>

  <svg class="badge" style="top:384px;" viewBox="0 0 112 112">
    <defs><path id="arcC" d="M15.6 70.7A43 43 0 1 1 96.4 70.7"/></defs>
    <circle cx="56" cy="56" r="33" fill="#fff" stroke="var(--purple)" stroke-width="3"/>
    <circle cx="56" cy="56" r="25" fill="#f1dcd6" role="img" aria-label="Crossed-out bed bug"/>
    <text class="badge-label" fill="var(--purple)"><textPath href="#arcC" startOffset="50%" text-anchor="middle">REPELS DUST MITES &amp; BED BUGS</textPath></text>
  </svg>

  <div class="photo-mattress" role="img" aria-label="White mattress on a black base"></div>

  <div class="contact">
    <p class="contact-phone">Call: 555 018 2460</p>
    <p class="contact-mail">or send us a mail: hello@willownestsleep.com</p>
  </div>

  <svg class="band band--bottom" viewBox="0 0 541 110" preserveAspectRatio="none">
    <path d="M0 30Q270 80 541 20V110H0Z" fill="var(--purple)"/>
    <path d="M0 24Q270 74 541 14V22Q270 82 0 32Z" fill="var(--purple-soft)"/>
  </svg>
</section>

</body>
</html>
```